Label for kQm Ranch beef tallow

I need a small label to go on a 2oz amber glass jar as well as a 4 oz. amber glass jar of moisturizer.
I prefer it to be rectangular for the 2oz jar since it's small and square for the 4oz jar.
I'd like to keep our kQm Ranch logo the same font and style, which is attached. Ten Sleep, Wyoming should be left out. The font for kQm Ranch is spartan.
The label content is as follows:
Signature Tallow
Whipped Moisturizer
Ingredients: Beef Tallow, jojoba oil, peppermint oil.
2oz. jar

Instead of a white label, I'm thinking of a tan or brown label that will blend in with the amber jar. The lettering could then be a white, cream or even rust/burgandy color. Something to give it a rich look.

Thank you!

Target Market(s)

Mainly women but men as well.

Industry/Entity Type

Ranching and online beef sales

Requirements
Must have
• kQm Ranch logo

```html
<!DOCTYPE html>
<html lang="en">
<head>
<meta charset="UTF-8">
<title>kQm Ranch – Signature Tallow Labels</title>
<link rel="stylesheet" href="https://fonts.googleapis.com/css2?family=League+Spartan:wght@300;400;500;600&display=swap">
<style>
  :root {
    --backdrop: #e6e6e6;
    --label: #ffffff;
    --ink: #111111;
    --band-text: #ffffff;
    --art-light: #f1f1f1;
    --art-dark: #9a9a9a;
  }
  * { box-sizing: border-box; margin: 0; padding: 0; }
  html, body {
    width: 1200px;
    height: 1200px;
    overflow: hidden;
    background: var(--backdrop);
    font-family: "League Spartan", "Helvetica Neue", Arial, sans-serif;
    color: var(--ink);
  }
  .canvas { position: relative; width: 1200px; height: 1200px; }

  .label {
    position: absolute;
    background: var(--label);
    overflow: hidden;
  }
  .label > * { position: absolute; }

  .title { font-weight: 300; letter-spacing: 0.02em; white-space: nowrap; }
  .brand { font-weight: 400; line-height: 0.9; text-align: center; white-space: nowrap; }
  .brand .brand-main { display: block; }
  .brand .brand-sub { display: block; }
  .bull-art {
    background: radial-gradient(ellipse at 50% 55%, var(--art-dark) 0%, var(--art-light) 75%);
    border-radius: 10px;
  }
  .band {
    left: 0; right: 0;
    background: var(--ink);
    color: var(--band-text);
    font-weight: 500;
    text-align: center;
    letter-spacing: 0.02em;
    display: flex; align-items: center; justify-content: center;
  }
  .ingredients { font-weight: 600; white-space: nowrap; }
  .size { font-weight: 600; text-align: center; left: 0; right: 0; }

  /* 2oz rectangular label */
  .label--small { left: 88px; top: 470px; width: 480px; height: 260px; border-radius: 32px; }
  .label--small .title { left: 27px; top: 24px; font-size: 20px; }
  .label--small .ingredients { left: 33px; top: 120px; font-size: 15px; line-height: 1.2; }
  .label--small .brand { left: 160px; top: 56px; width: 180px; }
  .label--small .brand-main { font-size: 76px; }
  .label--small .brand-sub { font-size: 34px; margin-top: 4px; }
  .label--small .bull-art { left: 338px; top: 110px; width: 126px; height: 88px; }
  .label--small .band { top: 198px; height: 28px; font-size: 20px; }
  .label--small .size { top: 236px; font-size: 14px; }

  /* 4oz square label */
  .label--large { left: 632px; top: 360px; width: 480px; height: 480px; border-radius: 36px; }
  .label--large .title { left: 0; right: 0; text-align: center; top: 38px; font-size: 31px; }
  .label--large .brand { left: 100px; top: 110px; width: 250px; }
  .label--large .brand-main { font-size: 118px; }
  .label--large .brand-sub { font-size: 50px; margin-top: 10px; }
  .label--large .bull-art { left: 335px; top: 240px; width: 120px; height: 116px; }
  .label--large .band { top: 357px; height: 40px; font-size: 30px; }
  .label--large .ingredients { left: 0; right: 0; text-align: center; top: 408px; font-size: 19px; }
  .label--large .size { top: 446px; font-size: 17px; }
</style>
</head>
<body>
<main class="canvas">

  <section class="label label--small" aria-label="2oz jar label">
    <p class="title">SIGNATURE TALLOW</p>
    <p class="ingredients">Ingredients:<br>Beef Tallow,<br>jojoba oil,<br>peppermint oil</p>
    <h1 class="brand"><span class="brand-main">kQm</span><span class="brand-sub">Ranch</span></h1>
    <div class="bull-art" role="img" aria-label="Line illustration of a standing bull"></div>
    <p class="band">WHIPPED MOISTURIZER</p>
    <p class="size">2oz.</p>
  </section>

  <section class="label label--large" aria-label="4oz jar label">
    <p class="title">SIGNATURE TALLOW</p>
    <h2 class="brand"><span class="brand-main">kQm</span><span class="brand-sub">Ranch</span></h2>
    <div class="bull-art" role="img" aria-label="Line illustration of a standing bull"></div>
    <p class="band">WHIPPED MOISTURIZER</p>
    <p class="ingredients">Beef Tallow, jojoba oil, peppermint oil</p>
    <p class="size">4oz.</p>
  </section>

</main>
</body>
</html>
```